Smile club flyer design

I am launching an office smile club and would like a design that sits my branding and that is appealing to customers. I have a design (I need a new one) that has all the information.
My website is maplehavendentalcarekx.com
Brand color is green. The design can be any color

Target Market(s)

Ages 30+

Industry/Entity Type

Dental

Font styles to use
Serif

Requirements
Must have
• Appealing to patients

```html
<!DOCTYPE html>
<html lang="en">
<head>
<meta charset="utf-8">
<title>Maplehaven Dental Care – Smile Club Membership</title>
<link href="https://fonts.googleapis.com/css2?family=Playfair+Display:wght@600;700&family=Montserrat:wght@400;500;600;800;900&family=Poppins:wght@700;800&display=swap" rel="stylesheet">
<style>
  :root{
    --stage:#5e5e5e;
    --paper:#eefaf7;
    --brand-green:#138a3e;
    --navy:#0f1d4a;
    --gold:#c8922f;
    --gold-light:#e2b45a;
    --gold-pale:#f4e6c8;
    --white:#ffffff;
    --ink:#22272e;
    --teal:#2aa7ae;
    --plum:#c9413f;
  }
  *{box-sizing:border-box;margin:0;padding:0}
  html,body{width:923px;height:1200px;overflow:hidden;background:var(--stage)}
  .canvas{position:relative;width:923px;height:1200px;background:var(--stage);font-family:"Montserrat",sans-serif}
  .flyer{position:absolute;left:125px;top:122px;width:683px;height:966px;background:var(--paper);overflow:hidden}
  .top-band{position:absolute;left:0;top:0;width:683px;height:16px}
  .brand{position:absolute;left:0;top:50px;width:683px;text-align:center;color:var(--brand-green);font-family:"Playfair Display",serif;font-weight:700}
  .brand-name{font-size:46px;line-height:1}
  .brand-sub{font-size:20px;letter-spacing:6px;margin-top:6px;line-height:1}
  .introducing{position:absolute;left:114px;top:154px;width:454px;height:53px;
    background:linear-gradient(90deg,rgba(200,146,47,0) 0%,var(--gold) 22%,var(--gold) 78%,rgba(200,146,47,0) 100%);
    color:var(--white);font-family:"Poppins",sans-serif;font-weight:800;font-size:32px;letter-spacing:5px;
    display:flex;align-items:center;justify-content:center}
  .club-name{position:absolute;left:0;top:236px;width:683px;text-align:center;color:var(--navy);font-family:"Playfair Display",serif;font-weight:700}
  .club-smile{font-size:150px;line-height:1}
  .club-word{font-size:46px;letter-spacing:10px;line-height:1;margin-top:30px}
  .membership-tab{position:absolute;left:182px;top:530px;width:319px;height:50px;background:var(--gold);
    border-radius:5px 5px 0 0;color:var(--white);font-family:"Poppins",sans-serif;font-weight:800;font-size:31px;letter-spacing:3px;
    display:flex;align-items:center;justify-content:center}
  .plans-band{position:absolute;left:0;top:580px;width:683px;height:230px;background:var(--navy)}
  .plans-heading{position:absolute;left:0;top:12px;width:683px;text-align:center;color:var(--white);font-family:"Poppins",sans-serif;font-weight:800;font-size:19px}
  .plans{position:absolute;left:17px;top:630px;width:649px;height:213px;display:flex;border-radius:4px;overflow:hidden;
    background:linear-gradient(135deg,var(--gold) 0%,var(--gold-light) 50%,var(--gold) 100%)}
  .plan{position:relative;height:100%;display:flex;flex-direction:column;border-right:1px solid rgba(255,255,255,.25)}
  .plan:last-child{border-right:none}
  .plan-core{width:159px}.plan-bright{width:154px}.plan-total{width:163px}.plan-refresh{width:173px}
  .plan-title{height:56px;border-bottom:1px solid rgba(255,255,255,.45);text-align:center;color:var(--white);padding-top:10px;line-height:1.05}
  .plan-title b{display:block;font-family:"Poppins",sans-serif;font-weight:800;font-size:17px}
  .plan-title span{display:block;font-weight:400;font-size:17px}
  .plan-features{list-style:none;padding:16px 6px 0 9px;flex:1;color:var(--white);font-size:9.6px;font-weight:500;line-height:1.3}
  .plan-features li{position:relative;padding-left:10px;margin-bottom:5px}
  .plan-features li::before{content:"✓";position:absolute;left:0;top:1px;width:7px;height:7px;border-radius:50%;background:rgba(255,255,255,.35);font-size:5px;line-height:7px;text-align:center}
  .plan-price{height:59px;border-top:1px solid rgba(255,255,255,.45);display:flex;align-items:center;justify-content:center;color:var(--white);font-family:"Poppins",sans-serif;font-weight:800}
  .plan-price strong{font-size:36px}
  .plan-price small{font-size:9px;margin-left:3px;margin-top:14px}
  .badge-new{position:absolute;right:10px;top:109px;width:41px;height:41px;border-radius:50%;background:radial-gradient(circle at 50% 30%,#5a5a5a,#111);color:var(--white);font-size:12px;font-weight:700;display:flex;align-items:center;justify-content:center}
  .join{position:absolute;left:34px;top:878px;width:306px;text-align:center}
  .join-title{font-family:"Poppins",sans-serif;font-weight:700;font-size:21px;color:var(--ink);letter-spacing:1px;line-height:1}
  .join-phone{display:flex;align-items:center;justify-content:center;margin-top:6px;color:var(--teal);font-family:"Poppins",sans-serif;font-weight:800;font-size:36px;line-height:1}
  .join-phone svg{margin-right:3px}
  .divider{position:absolute;left:366px;top:880px;width:1px;height:42px;background:#9aa}
  .finance{position:absolute;left:376px;top:874px;width:300px;text-align:center}
  .finance-label{font-weight:800;font-size:12px;letter-spacing:1px;color:var(--ink)}
  .finance-partners{display:flex;justify-content:center;gap:24px;margin-top:8px;align-items:center}
  .partner{display:flex;align-items:center;gap:5px;font-weight:600;font-size:20px;line-height:1}
  .partner-flexipay{color:var(--brand-green)}
  .partner-plumly{color:var(--plum)}
  .partner i{display:block;width:12px;height:12px}
  .partner-flexipay i{background:var(--brand-green);border-radius:50%}
  .partner-plumly i{background:var(--plum)}
  .finance-note{margin-top:7px;font-size:6.6px;font-weight:800;color:var(--ink)}
  .finance-note span{font-weight:600}
</style>
</head>
<body>
<div class="canvas">
  <div class="flyer">
    <svg class="top-band" viewBox="0 0 683 16" aria-hidden="true"><polygon points="0,2 683,0 683,3 0,15" fill="#c8922f"/></svg>

    <div class="brand">
      <div class="brand-name">Maplehaven</div>
      <div class="brand-sub">DENTAL CARE</div>
    </div>

    <div class="introducing">INTRODUCING</div>

    <div class="club-name">
      <div class="club-smile">Smile</div>
      <div class="club-word">CLUB</div>
    </div>

    <div class="membership-tab">MEMBERSHIP</div>

    <div class="plans-band">
      <p class="plans-heading">AFFORDABLE DENTAL CARE NO INSURANCE REQUIRED</p>
    </div>

    <div class="plans">
      <section class="plan plan-core">
        <h2 class="plan-title"><b>CORE CARE</b><span>PREVENTIVE</span></h2>
        <ul class="plan-features">
          <li>Comprehensive Annual Exam</li>
          <li>2 Professional Cleanings per Year</li>
          <li>Routine Bitewing X-rays</li>
          <li>10% Savings on Treatment</li>
        </ul>
        <div class="plan-price"><strong>$39</strong><small>/MONTH</small></div>
      </section>
      <section class="plan plan-bright">
        <h2 class="plan-title"><b>BRIGHT</b><span>COSMETIC</span></h2>
        <ul class="plan-features">
          <li>Annual In-Office Whitening (Top &amp; Bottom)</li>
          <li>Custom Whitening Trays</li>
          <li>15% Savings on Elective Treatment</li>
        </ul>
        <div class="plan-price"><strong>$59</strong><small>/MONTH</small></div>
      </section>
      <section class="plan plan-total">
        <h2 class="plan-title"><b>TOTAL SMILE</b><span>PERIODONTAL</span></h2>
        <ul class="plan-features">
          <li>3-4 Perio Maintenance Visits per Year</li>
          <li>1 Comprehensive Exam</li>
          <li>Diagnostic X-rays</li>
          <li>15% Savings on Restorative &amp; Elective Care</li>
        </ul>
        <div class="plan-price"><strong>$89</strong><small>/MONTH</small></div>
      </section>
      <section class="plan plan-refresh">
        <h2 class="plan-title"><b>SMILE REFRESH</b><span>PACKAGE</span></h2>
        <ul class="plan-features">
          <li>Cleaning + Comprehensive Exam + Whitening</li>
          <li>Limited Time Offer</li>
        </ul>
        <div class="badge-new">New</div>
        <div class="plan-price"><strong>$499</strong><small>/MONTH</small></div>
      </section>
    </div>

    <div class="join">
      <p class="join-title">JOIN SMILE CLUB TODAY!</p>
      <p class="join-phone">
        <svg width="30" height="30" viewBox="0 0 24 24" aria-hidden="true"><circle cx="12" cy="12" r="12" fill="#2aa7ae"/><path d="M8.2 6.5c.4-.4 1-.4 1.3 0l1.2 1.6c.3.4.2.9-.1 1.2l-.7.7c.5 1.2 1.5 2.2 2.7 2.7l.7-.7c.3-.3.8-.4 1.2-.1l1.6 1.2c.4.3.4.9 0 1.3l-.9.9c-.6.6-1.5.8-2.3.4-2.5-1.1-4.5-3.1-5.6-5.6-.4-.8-.2-1.7.4-2.3z" fill="#fff"/></svg>
        555-014-7282
      </p>
    </div>

    <div class="divider"></div>

    <div class="finance">
      <p class="finance-label">FLEXIBLE FINANCING FOR TREATMENT :</p>
      <div class="finance-partners">
        <span class="partner partner-flexipay"><i></i>FlexiPay</span>
        <span class="partner partner-plumly"><i></i>Plumly</span>
      </div>
      <p class="finance-note">PAYMENT PLANS AVAILABLE <span>|*$49 Lifetime Activation Fee (Non-Refundable)</span></p>
    </div>
  </div>
</div>
</body>
</html>
```